3 x Product Labels (nutritional supplements)

we need 3 x product labels designed. all labels will be the same dimensions and can incorporate a similar theme but ultimately the name and information is different (supplied) we would like to incorporate the existing product artwork into the labels also maybe changing the colors to suit the theme. not sure on those little details and need help.

Supplement

```html
<!DOCTYPE html>
<html lang="en">
<head>
<meta charset="utf-8">
<title>Vitalcore Nutrition – Supplement Labels</title>
<link href="https://fonts.googleapis.com/css2?family=Open+Sans:wght@400;600;700;800&display=swap" rel="stylesheet">
<style>
  :root {
    --bg: #ffffff;
    --label-white: #ffffff;
    --ink: #1a1a1a;
    --band-purple: #5a3d97;
    --band-blue: #3b57a6;
    --band-teal: #1f8f86;
    --band-green: #3aa66a;
    --red: #e3342a;
    --red-accent: #f5b432;
    --blue: #2f5aa6;
    --blue-accent: #b3cdf2;
    --orange: #e8782a;
    --orange-accent: #ffd84a;
    --brand-dot: #e0592a;
  }
  html, body {
    margin: 0;
    width: 1200px;
    height: 1200px;
    overflow: hidden;
    background: var(--bg);
  }
  .label-set {
    width: 1200px;
    height: 1200px;
    display: flex;
    align-items: center;
    justify-content: center;
    gap: 24px;
  }
  .product-label {
    width: 360px;
    height: 460px;
    box-shadow: 0 0 0 1px #e6e6e6;
    font-family: "Open Sans", sans-serif;
  }
  .product-label svg { display: block; }
  .brand-name { font-weight: 800; font-size: 27px; fill: var(--ink); letter-spacing: -0.5px; }
  .brand-sub { font-weight: 400; font-size: 13px; fill: var(--ink); }
  .product-title { font-weight: 800; font-size: 56px; fill: #fff; }
  .product-claim { font-weight: 700; font-size: 13.5px; }
  .tablet-type { font-weight: 600; font-size: 15px; fill: var(--ink); }
  .tablet-count { font-weight: 700; font-size: 26px; fill: #fff; }
  .listing-no { font-weight: 600; font-size: 8px; fill: var(--ink); letter-spacing: 0.5px; }
  .label--red .panel, .label--red .count-box { fill: var(--red); }
  .label--red .product-claim { fill: var(--red-accent); }
  .label--blue .panel, .label--blue .count-box { fill: var(--blue); }
  .label--blue .product-claim { fill: var(--blue-accent); }
  .label--orange .panel, .label--orange .count-box { fill: var(--orange); }
  .label--orange .product-claim { fill: var(--orange-accent); }
</style>
</head>
<body>
<main class="label-set">
  <svg width="0" height="0" style="position:absolute">
    <defs>
      <linearGradient id="bandTop" x1="0" x2="1" y1="0" y2="0">
        <stop offset="0" stop-color="var(--band-purple)"/>
        <stop offset="0.5" stop-color="var(--band-blue)"/>
        <stop offset="1" stop-color="var(--band-green)"/>
      </linearGradient>
      <linearGradient id="bandBottom" x1="0" x2="1" y1="0" y2="0">
        <stop offset="0" stop-color="var(--band-teal)"/>
        <stop offset="0.6" stop-color="var(--band-blue)"/>
        <stop offset="1" stop-color="var(--band-purple)"/>
      </linearGradient>
    </defs>
  </svg>

  <!-- Test Booster -->
  <article class="product-label label--red">
    <svg width="360" height="460" viewBox="0 0 360 460">
      <rect width="360" height="460" fill="var(--label-white)"/>
      <text class="brand-name" x="28" y="58">Vitalcore</text>
      <circle cx="168" cy="50" r="8" fill="var(--brand-dot)"/>
      <text class="brand-sub" x="29" y="74">Nutrition</text>
      <polygon points="0,118 360,56 360,72 0,132" fill="var(--band-green)"/>
      <polygon points="0,130 360,70 360,84 0,144" fill="url(#bandTop)"/>
      <polygon class="panel" points="0,142 360,82 360,310 0,365"/>
      <polygon points="0,365 360,310 360,324 0,381" fill="url(#bandBottom)"/>
      <polygon points="0,381 360,324 360,334 0,402" fill="var(--band-green)"/>
      <text class="product-title" x="180" y="190" text-anchor="middle">Test</text>
      <text class="product-title" x="180" y="248" text-anchor="middle">Booster</text>
      <text class="product-claim" x="180" y="282" text-anchor="middle">May Support Male Physiology</text>
      <text class="product-claim" x="180" y="301" text-anchor="middle">and Function Healthy and Increase</text>
      <text class="product-claim" x="180" y="320" text-anchor="middle">Testosterone Levels in Men</text>
      <text class="listing-no" transform="translate(340,330) rotate(90)">AUST L 418207</text>
      <text class="tablet-type" x="250" y="430" text-anchor="end">Film Coated Tablets</text>
      <rect class="count-box" x="262" y="402" width="46" height="42" rx="3"/>
      <text class="tablet-count" x="285" y="433" text-anchor="middle">60</text>
    </svg>
  </article>

  <!-- Mens Essential -->
  <article class="product-label label--blue">
    <svg width="360" height="460" viewBox="0 0 360 460">
      <rect width="360" height="460" fill="var(--label-white)"/>
      <text class="brand-name" x="28" y="58">Vitalcore</text>
      <circle cx="168" cy="50" r="8" fill="var(--brand-dot)"/>
      <text class="brand-sub" x="29" y="74">Nutrition</text>
      <polygon points="0,118 360,56 360,72 0,132" fill="var(--band-green)"/>
      <polygon points="0,130 360,70 360,84 0,144" fill="url(#bandTop)"/>
      <polygon class="panel" points="0,142 360,82 360,310 0,365"/>
      <polygon points="0,365 360,310 360,324 0,381" fill="url(#bandBottom)"/>
      <polygon points="0,381 360,324 360,334 0,402" fill="var(--band-green)"/>
      <text class="product-title" x="180" y="190" text-anchor="middle">Mens</text>
      <text class="product-title" x="180" y="248" text-anchor="middle">Essential</text>
      <text class="product-claim" x="180" y="282" text-anchor="middle">Vitamins, Herbs &amp; Minerals A</text>
      <text class="product-claim" x="180" y="301" text-anchor="middle">Multivitamin Complex Designed to Boost</text>
      <text class="product-claim" x="180" y="320" text-anchor="middle">Libido &amp; Increase Sexual Desire</text>
      <text class="listing-no" transform="translate(340,330) rotate(90)">AUST L 418207</text>
      <text class="tablet-type" x="250" y="430" text-anchor="end">Film Coated Tablets</text>
      <rect class="count-box" x="262" y="402" width="46" height="42" rx="3"/>
      <text class="tablet-count" x="285" y="433" text-anchor="middle">60</text>
    </svg>
  </article>

  <!-- Hair Essential -->
  <article class="product-label label--orange">
    <svg width="360" height="460" viewBox="0 0 360 460">
      <rect width="360" height="460" fill="var(--label-white)"/>
      <text class="brand-name" x="28" y="58">Vitalcore</text>
      <circle cx="168" cy="50" r="8" fill="var(--brand-dot)"/>
      <text class="brand-sub" x="29" y="74">Nutrition</text>
      <polygon points="0,118 360,56 360,72 0,132" fill="var(--band-green)"/>
      <polygon points="0,130 360,70 360,84 0,144" fill="url(#bandTop)"/>
      <polygon class="panel" points="0,142 360,82 360,310 0,365"/>
      <polygon points="0,365 360,310 360,324 0,381" fill="url(#bandBottom)"/>
      <polygon points="0,381 360,324 360,334 0,402" fill="var(--band-green)"/>
      <text class="product-title" x="180" y="190" text-anchor="middle">Hair</text>
      <text class="product-title" x="180" y="248" text-anchor="middle">Essential</text>
      <text class="product-claim" x="180" y="282" text-anchor="middle">Vitamins, Herbs &amp; Minerals</text>
      <text class="product-claim" x="180" y="301" text-anchor="middle">A Multivitamin Complex Designed to</text>
      <text class="product-claim" x="180" y="320" text-anchor="middle">Support Healthy Hair Growth</text>
      <text class="listing-no" transform="translate(340,330) rotate(90)">AUST L 418207</text>
      <text class="tablet-type" x="250" y="430" text-anchor="end">Film Coated Tablets</text>
      <rect class="count-box" x="262" y="402" width="46" height="42" rx="3"/>
      <text class="tablet-count" x="285" y="433" text-anchor="middle">60</text>
    </svg>
  </article>
</main>
</body>
</html>
```